New Coffee Brand Packaging Design

We need a package design for our new coffee brand called Marrowind Coffee. Our brand mission will be displayed on the packaging (along the side or the back) and we currently have a logo that should be displayed on the front. Feel free to suggest a new logo design as you are designing the packaging if it doesn't fit with your vision. The final design should be creative and conservative. We like coffee colors (dark and light browns, white, cream, black, gold). We also like chalkboard art imagery (i.e. coffee cups, theme words from our mission, people, etc.). One famous person from East Harbordale, OR is Desmond Okafor (world famous boxer and activist). If there is a way to draw his image in more of an abstract way where it doesn't infringe any patents that would be the sort of creativity we would like in the packaging. Our coffee brand prides itself on being a coffee for the people. For the average joe, working American who enjoys a good cup of coffee and a good atmosphere.

Marrowind Coffee Mission: "We aim to be a coffee company for the people. The people who have an appreciation and love for family, community and who never forget where they came from. Our coffee was born out of East Harbordale, OR…a place like many others where the hearts, the minds and the wills are strong. We hope you enjoy each and every cup. Peace & Blessings."

Reason: Extending the deadline to see if there are more design ideas.

Requirements
Must have
• (On the side or on the back of the packaging) Marrowind Coffee Mission: "We aim to be a coffee company for the people. The people who have an appreciation and love for family, community and who never forget where they came from. Our coffee was born out of East Harbordale, OR…a place like many others where the hearts, the minds and the wills are strong. We hope you enjoy each and every cup. Peace & Blessings."
Nice to have
• Coffee Colors: dark and light browns, white, cream, black, gold

```html
<!DOCTYPE html>
<html lang="en">
<head>
<meta charset="utf-8">
<title>Marrowind Coffee – Mission Panel</title>
<link rel="stylesheet" href="https://fonts.googleapis.com/css2?family=Patrick+Hand+SC&display=swap">
<style>
  :root {
    --roast-dark: #120906;
    --roast-shade: #1d100b;
    --cream: #f4e4c6;
  }
  html, body {
    margin: 0;
    padding: 0;
    width: 750px;
    height: 1200px;
    overflow: hidden;
    background: var(--roast-dark);
  }
  .panel {
    position: relative;
    width: 750px;
    height: 1200px;
    background: var(--roast-dark);
    color: var(--cream);
    font-family: "Patrick Hand SC", cursive;
    overflow: hidden;
  }
  .bean-backdrop {
    position: absolute;
    inset: 0;
    background:
      radial-gradient(ellipse 300px 520px at 300px 330px, var(--roast-shade) 0%, rgba(29,16,11,0) 70%),
      radial-gradient(ellipse 260px 440px at 640px 560px, var(--roast-shade) 0%, rgba(29,16,11,0) 70%),
      radial-gradient(ellipse 320px 480px at 260px 960px, var(--roast-shade) 0%, rgba(29,16,11,0) 70%);
  }
  .mission {
    position: absolute;
    left: 90px;
    top: 280px;
    width: 500px;
    margin: 0;
    font-size: 27px;
    line-height: 41px;
    letter-spacing: 1.2px;
  }
  .mission p {
    margin: 0 0 41px;
  }
  .mission .line {
    display: block;
    white-space: nowrap;
  }
  .mission .sign-off {
    font-size: 36px;
    line-height: 44px;
    margin: -4px 0 0;
  }
  .brand-mark {
    position: absolute;
    left: 444px;
    top: 1030px;
    width: 240px;
    text-align: center;
  }
  .brand-name {
    display: block;
    font-size: 44px;
    line-height: 50px;
  }
  .brand-descriptor {
    display: block;
    font-size: 15px;
    letter-spacing: 1px;
  }
</style>
</head>
<body>
  <main class="panel">
    <div class="bean-backdrop" role="img" aria-label="Faint large coffee bean shapes across the dark background"></div>

    <section class="mission">
      <p>
        <span class="line">We aim to be a coffee company for</span>
        <span class="line">the people. The people who have an</span>
        <span class="line">appreciation and love for family,</span>
        <span class="line">community and who never forget</span>
        <span class="line">where they came from. Our coffee</span>
        <span class="line">was born out of East Harbordale, OR.</span>
      </p>
      <p>
        <span class="line">A place like many others where the</span>
        <span class="line">hearts, the minds and the wills are</span>
        <span class="line">strong. We hope you enjoy each and</span>
        <span class="line">every cup.</span>
      </p>
      <p class="sign-off">Peace &amp; Blessings.</p>
    </section>

    <footer class="brand-mark">
      <span class="brand-name">Marrowind</span>
      <span class="brand-descriptor">coffee</span>
    </footer>
  </main>
</body>
</html>
```